Website for the posting of RFQ from companies

BRIGHTOWL, a website for posting RFQ from government and companies.
Slogan: Promoting ethical and transparent business practices

Designed in HTML5 and responsive.
Government and companies can upload RFQ (request for quotation) advertisements through a back-end which can be searchable by companies interested in submitting quotes to the companies.

Companies once registered, get a username and logon to access back-end to load their advertisements for RFQ.

Users/ entrepreneurs also register and based on their subscription can access certain advertised RFQ information.

Also a platform where companies can notify other businesses of their commodities on hand. Example small mining company, small fishing company, farm growing fruits and veggies.

Weekly newsletter with latest uploaded RFQ information sent to users.
RFQ advert should display how often it was viewed. also display a button to contact company for more information.

Users register to receive sms and email notification when tenders of interest posted in their categories/ industry of interest.

Competitors:
Qu-biddesk.co.za
Rbidhouse.gov.za
Quickbidroom.co.za
Bidpilotx.co.za
Marketvine.net

Target Market(s)

Business people

Industry/Entity Type

Business

Coding

Coded - Design and coding required

Number of Pages Required

5+ page

Font styles to use
Sans Serif

Requirements
Must have
• simple clean design
• Html5
• Responsive
Nice to have
• Better and improved Design compared to my competitors
• Use of African models in pictures
Should not have
• dark background

```html
<!DOCTYPE html>
<html lang="en">
<head>
<meta charset="utf-8">
<title>Brightowl Trading – Request for Quotation Portal</title>
<link href="https://fonts.googleapis.com/css2?family=Open+Sans:wght@400;600;700&family=Raleway:wght@300;400&display=swap" rel="stylesheet">
<style>
  :root{
    --black:#000000;
    --ink:#222222;
    --text:#333333;
    --muted:#a8a8a8;
    --white:#ffffff;
    --orange:#f7941d;
    --orange-deep:#f08a00;
    --red:#f0311b;
    --red-soft:#ee4346;
    --grey-bg:#f1f1f1;
    --pill:#2b2b2b;
    --footer-bar:#111111;
  }
  *{box-sizing:border-box;margin:0;padding:0}
  html,body{width:1200px;height:2261px;overflow:hidden}
  body{position:relative;background:var(--white);font-family:"Open Sans",Arial,sans-serif;color:var(--text)}
  .abs{position:absolute}
  a{text-decoration:none}

  /* Header */
  .site-header{left:0;top:0;width:1200px;height:99px;background:var(--black)}
  .brand{left:138px;top:26px;color:var(--white);font-size:22px;font-weight:600;letter-spacing:2px;display:flex;align-items:center;gap:10px;line-height:26px}
  .brand-mark{width:11px;height:11px;background:var(--orange)}
  .slogan{left:159px;top:58px;color:var(--muted);font-size:11px;letter-spacing:.4px}
  .lang{left:985px;top:12px;color:var(--muted);font-size:12px}
  .btn-pill{top:40px;height:31px;border-radius:16px;background:var(--pill);color:var(--white);font-size:13px;display:flex;align-items:center;justify-content:center}
  .btn-join{left:713px;width:82px}
  .btn-login{left:803px;width:82px}
  .call{left:898px;top:47px;color:#cccccc;font-size:11px}
  .phone{left:948px;top:41px;color:var(--white);font-size:19px}

  /* Nav */
  .main-nav{left:0;top:99px;width:1200px;height:44px;background:var(--orange)}
  .nav-link{top:12px;color:var(--white);font-size:14px}
  .search{left:947px;top:105px;width:147px;height:32px;border-radius:16px;background:var(--white);display:flex;align-items:center;padding:0 14px;justify-content:space-between;color:#aaaaaa;font-size:12px}

  /* Hero */
  .hero{left:0;top:143px;width:1200px;height:518px;background:linear-gradient(180deg,#f1f4f6 0%,#dfe6ec 22%,#c3ccd4 42%,#98a3ad 58%,#7d8790 70%,#9a9995 80%,#b9b8b4 88%,#8e8d8a 100%)}
  .hero-title{left:0;top:274px;width:1200px;text-align:center;font-size:34px;font-weight:700;color:var(--ink);letter-spacing:1px}
  .hero-lead{left:305px;top:322px;width:590px;text-align:center;font-size:16.5px;line-height:21px;color:var(--ink)}
  .hero-countries{left:0;top:400px;width:1200px;text-align:center;font-size:11.5px;color:var(--ink)}
  .hero-input{left:400px;top:442px;width:252px;height:38px;border-radius:19px;background:var(--white);font-size:11px;color:#888888;padding:12px 19px;letter-spacing:.3px}
  .hero-btn{left:659px;top:442px;width:141px;height:38px;border-radius:19px;background:var(--orange);color:var(--white);font-size:16px;display:flex;align-items:center;justify-content:center}
  .dots{left:558px;top:618px;display:flex;gap:5px}
  .dots span{width:12px;height:12px;border-radius:50%;background:var(--white)}

  /* Customer groups */
  .section-title{left:0;top:688px;width:1200px;text-align:center;font-size:22px;font-weight:600;color:var(--orange)}
  .group-heading{font-size:20px;font-weight:600;color:var(--ink);line-height:26px}
  .group-copy{font-size:12.3px;line-height:17.6px;color:var(--ink);text-align:left;hyphens:auto;-webkit-hyphens:auto}
  .btn-more{width:93px;height:36px;border-radius:18px;background:var(--orange);color:var(--white);font-size:12px;font-weight:600;display:flex;align-items:center;justify-content:center}
  .photo-frame{background:var(--white);box-shadow:0 0 4px rgba(0,0,0,.25);padding:14px}
  .photo-frame div{width:100%;height:100%}

  /* Grey band */
  .promo-band{left:0;top:1365px;width:1200px;height:468px;background:var(--grey-bg)}
  .band-heading{font-size:20px;font-weight:600;color:var(--ink)}
  .access-desc{left:628px;top:1430px;width:460px;font-size:11.5px;line-height:14px;color:var(--ink)}
  .access-box{width:143px;height:126px;color:var(--white);font-size:16px;font-weight:600;display:flex;align-items:center;justify-content:center;text-align:center;line-height:17px}
  .access-text{left:787px;width:296px;font-size:12px;line-height:14.8px;color:var(--ink);text-align:justify;hyphens:auto;-webkit-hyphens:auto}
  .access-more{left:787px;font-size:13px;color:var(--orange-deep)}

  /* Carousel */
  .thumb{top:1873px;width:114px;height:86px}
  .thumb-event{background:linear-gradient(160deg,#2d4f96 0%,#1d3672 45%,#e9edf4 52%,#1d3672 60%,#142a5c 100%)}
  .thumb-eye{background:linear-gradient(120deg,#f3f3f3 0%,#d2d7db 35%,#6f8ea6 50%,#d8dcdf 65%,#f4f4f4 100%)}

  /* Footer */
  .site-footer{left:0;top:2003px;width:1200px;height:212px;background:var(--black);color:var(--white)}
  .foot-heading{font-family:"Raleway","Open Sans",sans-serif;font-size:20px;font-weight:400;color:var(--white)}
  .foot-link{font-size:12px;color:var(--white)}
  .foot-line{font-size:12px;color:var(--white);line-height:19.5px}
  .help{font-weight:600}
  .map{left:641px;top:2036px;width:188px;height:162px;background:linear-gradient(135deg,#efe9dc 0%,#f4e27a 30%,#e8e2d2 45%,#d9d3c2 70%,#efe9dc 100%)}
  .news-input{left:863px;top:2066px;width:214px;height:35px;background:var(--white);font-size:11px;color:#999999;padding:11px 10px}
  .news-btn{left:863px;top:2114px;width:77px;height:26px;background:var(--red-soft);color:var(--white);font-size:11px;display:flex;align-items:center;justify-content:center}
  .footer-bar{left:0;top:2215px;width:1200px;height:46px;background:var(--footer-bar)}
  .social{top:2232px;width:11px;height:11px;border-radius:50%;background:var(--white)}
  .copyright{left:803px;top:2232px;font-size:10px;color:var(--white)}
  .version{left:1108px;top:2232px;font-size:10px;color:var(--white)}
</style>
</head>
<body>

<header class="abs site-header">
  <div class="abs brand"><span class="brand-mark"></span>BRIGHTOWL TRADING</div>
  <div class="abs slogan">Promoting ethical and transparent business practices</div>
  <div class="abs lang">Language : EN</div>
  <a class="abs btn-pill btn-join">Join Now</a>
  <a class="abs btn-pill btn-login">Login</a>
  <div class="abs call">Call Us :</div>
  <div class="abs phone">1- 800 555 0142</div>
</header>

<nav class="abs main-nav">
  <span class="abs nav-link" style="left:138px">Home</span>
  <span class="abs nav-link" style="left:210px">About Us</span>
  <span class="abs nav-link" style="left:300px">Services</span>
  <span class="abs nav-link" style="left:384px">Directory</span>
  <span class="abs nav-link" style="left:475px">News</span>
  <span class="abs nav-link" style="left:540px">Contact</span>
</nav>
<div class="abs search">Search
  <svg width="13" height="13" viewBox="0 0 13 13"><circle cx="5.5" cy="5.5" r="4" fill="none" stroke="#999" stroke-width="1.8"/><line x1="8.5" y1="8.5" x2="12" y2="12" stroke="#999" stroke-width="2"/></svg>
</div>

<section class="abs hero" role="img" aria-label="Businesswoman standing on a stone rooftop ledge looking out over a hazy city skyline and bay bridge"></section>
<h1 class="abs hero-title">BRIGHTOWL TRADING</h1>
<p class="abs hero-lead">This will enable entrepreneurs to search and view request for quotation (RFQ) and/or tender information advertised by governments, municipalities, NGOs and private companies in Southern Africa</p>
<p class="abs hero-countries">Namibia, South Africa, Botswana, Mozambique, Lesotho, Swaziland, Zimbabwe, Zambia and Angola</p>
<div class="abs hero-input">REQUEST FOR QUOTATION</div>
<div class="abs hero-btn">SEARCH NOW</div>
<div class="abs dots"><span></span><span></span><span></span><span></span><span></span></div>

<h2 class="abs section-title">THE TWO MAIN CUSTOMER GROUPS</h2>

<h3 class="abs group-heading" style="left:166px;top:772px">Entrepreneurs/tenderpreneurs.</h3>
<p class="abs group-copy" style="left:166px;top:817px;width:400px">Neque porro quisquam est, qui dolorem ipsum quia dolor sit amet, consectetur, adipisci velit, sed quia non numquam eius modi tempora incidunt ut labore et dolore magnam aliquam quaerat voluptatem. Ut enim ad minima veniam, quis nostrum exercitationem ullam corporis suscipit laboriosam, nisi ut aliquid ex ea commodi consequatur? Quis autem vel eum iure reprehenderit qui in ea voluptate velit esse quam nihil molestiae consequatur,</p>
<a class="abs btn-more" style="left:166px;top:982px">Read more</a>
<div class="abs photo-frame" style="left:627px;top:757px;width:404px;height:248px">
  <div role="img" aria-label="Young African woman in a colourful dress writing at a desk in a bright art studio" style="background:linear-gradient(100deg,#efeae4 0%,#d93a4f 12%,#ece7e0 24%,#e6e1da 38%,#3a2a24 48%,#c2533a 56%,#e4ded6 66%,#9c6a3e 82%,#f1ede7 100%)"></div>
</div>

<div class="abs photo-frame" style="left:159px;top:1068px;width:402px;height:248px">
  <div role="img" aria-label="Woman in glasses and a white blouse writing at an office desk" style="background:linear-gradient(100deg,#8d3a3e 0%,#c9c7c5 18%,#e9e8e6 35%,#f6f5f3 50%,#e2dfda 65%,#cdb79b 82%,#b49d80 100%)"></div>
</div>
<h3 class="abs group-heading" style="left:628px;top:1072px;width:420px">Governments, municipalities, NGOs, private companies and individuals.</h3>
<p class="abs group-copy" style="left:628px;top:1143px;width:400px">Neque porro quisquam est, qui dolorem ipsum quia dolor sit amet, consectetur, adipisci velit, sed quia non numquam eius modi tempora incidunt ut labore et dolore magnam aliquam quaerat voluptatem. Ut enim ad minima veniam, quis nostrum exercitationem ullam corporis suscipit laboriosam, nisi ut aliquid ex ea commodi consequatur? Quis autem vel eum iure reprehenderit qui in ea voluptate velit esse quam nihil molestiae consequatur,</p>
<a class="abs btn-more" style="left:630px;top:1298px">Read more</a>

<section class="abs promo-band"></section>
<h3 class="abs band-heading" style="left:162px;top:1403px">Advertising banners</h3>
<div class="abs" role="img" aria-label="Driver education programme advertising banner" style="left:159px;top:1467px;width:402px;height:103px;background:linear-gradient(180deg,#1f6e86 0%,#1b6179 88%,#e2b93b 88%,#e2b93b 94%,#17566b 94%)"></div>
<div class="abs" role="img" aria-label="Colourful camera lens advertisement" style="left:159px;top:1608px;width:114px;height:172px;background:radial-gradient(circle at 50% 50%,#3a2c5a 0%,#d8428a 18%,#f3c12a 34%,#f9b02a 60%,#f59a12 100%)"></div>
<div class="abs" role="img" aria-label="Spring jewellery collection advertisement" style="left:302px;top:1608px;width:115px;height:172px;background:linear-gradient(180deg,#d9d9d9 0%,#ececec 30%,#f6f6f6 60%,#d4d4d4 100%)"></div>
<div class="abs" role="img" aria-label="Wedding and lifestyle expo poster" style="left:446px;top:1608px;width:114px;height:172px;background:linear-gradient(180deg,#c8201f 0%,#b51b1b 60%,#f1eded 72%,#1a1a1a 85%,#8e1414 100%)"></div>

<h3 class="abs band-heading" style="left:628px;top:1393px">Access Types</h3>
<p class="abs access-desc">Access to the website will be based on the type of access that is requested, i.e. Basic or Advances access.</p>

<div class="abs access-box" style="left:628px;top:1473px;background:var(--orange)">Lite<br>Access</div>
<p class="abs access-text" style="top:1488px">only allows a user to register, create a profile and view tender information of that day. Previously loaded tender information will not be visible with this type of access.</p>
<span class="abs access-more" style="top:1561px">Read more</span>

<div class="abs access-box" style="left:628px;top:1629px;background:var(--red)">Premium<br>Access</div>
<p class="abs access-text" style="top:1632px">will be based on subscriptions of 3, 6, 12 or 24 months and will allow users to have access to all tender information, search facilities, disable profile from being visible to other users, access to view other profiles, notifications of new tenders or tenders of your interest, access to the social networking website, newsletter, job postings, product launches and events.</p>
<span class="abs access-more" style="top:1766px">Read more</span>

<div class="abs thumb thumb-event" role="img" aria-label="New year event graphic" style="left:131px"></div>
<div class="abs thumb thumb-eye" role="img" aria-label="Close-up eye campaign graphic" style="left:267px"></div>
<div class="abs thumb thumb-event" role="img" aria-label="New year event graphic" style="left:406px"></div>
<div class="abs thumb thumb-eye" role="img" aria-label="Close-up eye campaign graphic" style="left:541px"></div>
<div class="abs thumb thumb-event" role="img" aria-label="New year event graphic" style="left:680px"></div>
<div class="abs thumb thumb-eye" role="img" aria-label="Close-up eye campaign graphic" style="left:815px"></div>
<div class="abs thumb thumb-event" role="img" aria-label="New year event graphic" style="left:954px"></div>

<footer class="abs site-footer"></footer>
<h4 class="abs foot-heading" style="left:120px;top:2023px">Quick Links</h4>
<span class="abs foot-link" style="left:122px;top:2066px">Home</span>
<span class="abs foot-link" style="left:122px;top:2097px">About Us</span>
<span class="abs foot-link" style="left:122px;top:2128px">Services</span>
<span class="abs foot-link" style="left:122px;top:2159px">Directory</span>
<span class="abs foot-link" style="left:260px;top:2066px">News</span>
<span class="abs foot-link" style="left:260px;top:2097px">Contact Us</span>
<span class="abs foot-link" style="left:260px;top:2128px">Login</span>
<span class="abs foot-link" style="left:260px;top:2159px">Join Now</span>

<h4 class="abs foot-heading" style="left:433px;top:2020px">Contact Us</h4>
<p class="abs foot-line" style="left:433px;top:2062px">18 Acacia Park Road,<br>Suite 4<br>Pretoria,<br>GP 0181<br>800 555-0178</p>
<p class="abs foot-line" style="left:435px;top:2176px"><span class="help">Help Line</span>&nbsp;&nbsp;&nbsp; 1-800 - 555 - 0199</p>

<div class="abs map" role="img" aria-label="Street map showing the office location"></div>

<h4 class="abs foot-heading" style="left:862px;top:2022px">Newsletter</h4>
<div class="abs news-input">Enter email id</div>
<div class="abs news-btn">Subscribe</div>

<div class="abs footer-bar"></div>
<span class="abs social" style="left:111px" aria-label="Social link"></span>
<span class="abs social" style="left:145px" aria-label="Social link"></span>
<span class="abs social" style="left:181px" aria-label="Social link"></span>
<span class="abs social" style="left:212px" aria-label="Social link"></span>
<span class="abs copyright">© 2015 • www.brightowltrading.co.za • PRIVACY POLICY</span>
<span class="abs version">M1</span>

</body>
</html>
```